EXCITING DECK for Automotive dealers that shows how our Technology works.

General Concept
The deck should visually represent the Trade and Credit Lead Life Cycle program is a dynamic, interconnected journey, illustrating how leads are generated, nurtured, and converted. The focus should be on how your system flows seamlessly between credit and trade-in opportunities for consumers, with the goal of maximizing engagement and conversions.
Slide 1: Title Slide - Lead Life Cycle Program
• Visual Concept: A stylized cycle or wheel that represents the stages of the lead life cycle, with arrows connecting each stage.
• Headline: "Lead Life Cycle Program"
• Subhead line: "Credit Pre-Qualification and Trade-In Appraisal"
• Imagery: Modern, sleek graphics of vehicles, smartphones (for texting), email icons, and dollar signs for value.
Slide 2: Lead Generation Sources
• Visual Concept: A funnel with the top representing the different lead generation sources.
• Content:
o Top of Funnel (Leads Enter):
 Pre-Qualification Tool (Fast4Loan)- How it Works
 1. Converts Web Traffic into the highest quality lead on the market
 Vorqel Email/Mail Marketing – How it Works
 1. Delivers actionable leads from email marketing not Just OPENS AND CLICKS. Show the text demo. Audiences below
1. Past Sold Customers (Equity Targets)
2. Past Service Onlu Department Customers (Conquest Sales)
3. Unsold Leads (from previous interactions)
o Each source should have a distinct icon to represent it (e.g., envelope for email, a wrench for past service customers, etc.).
• Headline: "Multiple Lead Sources Feeding into the Program"
• Imagery: The funnel narrowing toward the next step with leads symbolized by icons flowing downward.
Slide 3: Credit Leads - Pre-Qualified Flow
• Visual Concept: A customer engaging with the Fast4Loan tool on their mobile, being pre-qualified, and then us sending a offer to appraise their trade.
• Flow Explanation:
o Customer pre-qualifies via Fast4Loan → Receives credit approval → Email and Mail Example to check trade-in value.
• Headline: "Pre-Qualified Leads: Offering Trade-In Appraisal"
• Imagery: A sequence that shows how a customer moves from pre-qualification to considering their trade-in value. To purchasing
Slide 4: Trade-In Leads - Valuation Flow
• Visual Concept: A customer who has received a trade-in valuation offer now being prompted to pre-qualify for financing.
• Flow Explanation:
o Customer texts for vehicle value → Receives trade-in appraisal → Offer to pre-qualify for financing appears link is at the bottom of the text response.
• Headline: "Trade-In Leads: Offering Credit Pre-Qualification"
• Imagery: A customer looking at their trade-in value on their phone and being shown an additional prompt to pre-qualify for a loan.
Slide 5: Cross-Offer Opportunities
• Visual Concept: A two-way street or cycle, illustrating the seamless transition between offering pre-qualification to trade-in customers and offering trade-in value to credit leads.
• Content:
o Two pathways:
1. Start as a Credit Lead → Offer Trade-In Valuation
2. Start as a Trade-In Lead → Offer Credit Pre-Qualification
o Headline: "Cross-Offer Opportunities for Maximum Engagement"
• Imagery: Arrows going in both directions, symbolizing the back-and-forth opportunities between credit and trade leads.
Digital Retargeting for Cross-Action Engagement
• Visual Concept: An omnichannel approach with a customer in the center, surrounded by email/Mail icons, Chatterbook, and Snapgrove logos. Arrows leading from each platform back to the customer, showing how these channels drive engagement.
• Content:
o Title: "Engage to Convert one lead type to get both with Email/Mail and Digital Retargeting"
o Explanation:
 Whether a lead starts as a Pre-Qualified Credit Lead or a Trade-In Valuation Lead, we use personalized Email/Mail Campaigns and Digital Retargeting Ads (Chatterbook & Snapgrove) to encourage them to take the next action.
 If they pre-qualify for credit, we retarget them with trade-in valuation offers.
 If they start with a trade-in valuation, we follow up with financing offers.
o Headline: "Leverage Email & Social Retargeting to Drive Cross-Action"
• Visuals:
o Icons of Email, Chatterbook, and Snapgrove: Showing the platforms through which you retarget leads.
o Customer Journey Map: Illustrating how leads who interacted once are guided to the next step (credit lead → trade-in offer, trade-in lead → pre-qualification).
o Arrows Flowing Between Channels: Showing how no matter where a lead starts, they are continually engaged through digital touchpoints until they complete both actions.
o Ad examples
• Call to Action: "Stay Top of Mind and Convert Leads into Multi-Action Customers"
This slide emphasizes how you’re leveraging both email/mail marketing and social media retargeting to move leads further along the customer journey, regardless of how they entered your funnel. The visuals should reinforce the idea of continuous engagement and omnipresent reminders for them to take action.
________________________________________
Slide 6: Lifecycle Representation
• Visual Concept: A circular diagram showing how leads can continuously move between credit and trade offers throughout their lifecycle.
• Content:
o Show how the lifecycle doesn’t end after one interaction, but can continue with follow-up offers.
o Headline: "Continuous Engagement Throughout the Lead Life Cycle"
• Imagery: Circular arrows or flowchart representing each stage looping back into the lifecycle, emphasizing that leads can be re-engaged.
Slide 7: Lead Conversion Goals
• Visual Concept: A progression from leads to successful transactions (e.g., a customer with keys to a new car). Showing that getting customers to take both of these actions delives a lead that is very committed to the process of buying.
• Content:
o End goal: Convert both credit and trade leads into sales.
o Show statistics or success metrics as optional data points.
o Headline: "Converting Leads into Sales"
• Imagery: A car dealership handing over keys, happy customers, and sold vehicles.
Slide 8: Next Steps / Call to Action
• Visual Concept: A final slide summarizing the key takeaways and next steps.
• Headline: "Maximize Lead Potential with Cross-Offer Opportunities"
• Imagery: A mix of credit leads, trade leads, and successful customer outcomes.
________________________________________These slides should be clean and modern, using simple but impactful visuals like arrows, icons, and flow diagrams to represent the journey. The key is to emphasize flow and interaction between credit and trade-in opportunities, showing the two-way cross-sell nature of your Lead Life Cycle Program.

I have attached a current deck so you can pull some basic product info and graphics into the new deck (PLEASE DONT JUST COPY THE OLD DECK). I have also included some of our email artwrok if you need it. If you want to look at our website go here www.plorvenadsgroup.example

Target Market(s)

Car Dealers

Industry/Entity Type

Automotive Marketing

Requirements
Must have
• PLEASE READ THE PROJECT DESCRIPTION
Nice to have
Should not have
• PLEASE dont just copy the deck i uploaded. I am looking for a differnt take.

```html
<!DOCTYPE html>
<html lang="en">
<head>
<meta charset="utf-8">
<title>Lead Life Cycle Program – Deck Overview</title>
<link href="https://fonts.googleapis.com/css2?family=Raleway:wght@300;400;500;600;700;800&display=swap" rel="stylesheet">
<style>
  :root{
    --red:#e2001a;
    --red-dark:#a50013;
    --pink:#f4a9b1;
    --ink:#333333;
    --charcoal:#3a3a3a;
    --black:#161616;
    --muted:#6b6b6b;
    --grey-light:#c9c9c9;
    --board:#545454;
    --white:#ffffff;
  }
  *{margin:0;padding:0;box-sizing:border-box}
  html,body{width:1021px;height:1200px;overflow:hidden;background:var(--board)}
  body{position:relative;font-family:"Raleway",sans-serif;color:var(--ink)}
  .slide{position:absolute;width:460px;height:259px;background:var(--white);overflow:hidden}
  .slide > *{position:absolute}
  .slide-title{left:15px;top:10px;font-size:14.5px;font-weight:800;line-height:17px;color:var(--ink);letter-spacing:.1px}
  .title-bar{left:0;top:8px;width:4.5px;height:23px;background:var(--red)}
  .footer{left:0;bottom:0;width:100%;height:18px;display:flex}
  .footer-left{width:371px;background:var(--red);color:var(--white);font-size:5.3px;font-weight:700;padding-left:16px;line-height:18px}
  .footer-right{flex:1;background:var(--charcoal);color:var(--white);font-size:5.3px;font-weight:700;padding-left:27px;line-height:18px}

  /* Cover */
  .cover{background:linear-gradient(135deg,#2a2c33 0%,#1c1d22 45%,#2e2a2a 100%)}
  .cover-brand{left:25px;top:40px;color:var(--white);font-size:10px;font-weight:600;letter-spacing:3px}
  .cover-brand-mark{left:49px;top:24px;width:12px;height:12px;background:var(--white)}
  .cover-bar{left:26px;top:162px;width:3.5px;height:59px;background:var(--red)}
  .cover-title{left:42px;top:158px;color:var(--white);font-size:19.5px;font-weight:800;line-height:24px}
  .cover-title span{color:var(--red)}
  .cover-sub{left:43px;top:211px;color:var(--white);font-size:8.6px;font-weight:500}
  .cycle{left:0;top:0;width:460px;height:259px}

  /* Conversion goals */
  .photo{background:linear-gradient(160deg,#6f7a80 0%,#8d7a66 45%,#3d4a62 100%)}
  .goals-photo{left:20px;top:46px;width:198px;height:178px}
  .goals-head{left:240px;top:54px;font-size:12px;font-weight:800;color:var(--red)}
  .metric{left:240px;width:194px;font-size:4.9px;color:var(--muted)}
  .metric-label{display:flex;justify-content:space-between}
  .metric-track{margin-top:4px;height:1.3px;background:var(--grey-light)}
  .metric-fill{height:1.3px;background:var(--charcoal)}

  /* Lead sources */
  .sources-art{left:0;top:0;width:460px;height:259px}
  .source-name{color:var(--white);font-size:7.6px;font-weight:700;line-height:12.5px}
  .source-copy{font-size:6.6px;font-weight:400;color:var(--muted);line-height:10.5px}
  .source-list{list-style:none;font-size:5.4px;color:var(--muted);line-height:10px}
  .source-list li::before{content:"";display:inline-block;width:4px;height:4px;border-radius:50%;background:var(--red);margin-right:5px;vertical-align:middle}
  .feed-line{font-size:6.8px;color:var(--ink);font-weight:500}

  /* Cross offer */
  .cross-photo{left:23px;top:54px;width:412px;height:171px;clip-path:polygon(21px 0,412px 0,390px 171px,0 171px);
    background:linear-gradient(90deg,#1f2028 0%,#2c2d36 30%,#7a6330 55%,#b0792c 72%,#c9c3a8 90%,#34353d 100%)}

  /* Credit flow */
  .flow-photo{left:20px;top:46px;width:198px;height:178px;background:linear-gradient(110deg,#b9754a 0%,#d8cfc6 45%,#eeeae6 100%)}
  .flow-head{left:241px;top:46px;font-size:11.8px;font-weight:800;color:var(--red);line-height:17px}
  .flow-art{left:0;top:0;width:460px;height:259px}
  .flow-step{left:242px;width:189px;text-align:center;color:var(--white);font-size:7.5px;line-height:11px}
  .flow-step b{display:block;font-size:7.8px;font-weight:800}

  /* Lifecycle */
  .life-sub{left:16px;top:31px;font-size:10.8px;font-weight:700;color:var(--red)}
  .life-art{left:0;top:0;width:460px;height:259px}
  .life-note{width:100px;text-align:center;font-size:5.2px;line-height:9.4px;color:var(--muted)}
  .life-note strong{display:block;font-size:6.4px;color:var(--black);font-weight:800;letter-spacing:.2px}
  .life-note.up strong{margin-top:3px}
  .life-note.down strong{margin-bottom:2px}
</style>
</head>
<body>

<!-- Slide: Title -->
<section class="slide cover" style="left:32px;top:34px">
  <div class="cover-brand-mark"></div>
  <div class="cover-brand">PLORVEN</div>
  <svg class="cycle" viewBox="0 0 460 259" aria-hidden="true">
    <path d="M243.2 161.7 A100 100 0 0 1 301.3 37 L318.2 79.8 A54 54 0 0 0 286.8 147.1 Z" fill="#e2001a"/>
    <path d="M306.3 35.2 A100 100 0 0 1 431 93.3 L388.2 110.2 A54 54 0 0 0 320.9 78.8 Z" fill="#ffffff"/>
    <path d="M432.8 98.3 A100 100 0 0 1 374.7 223 L357.8 180.2 A54 54 0 0 0 389.2 112.9 Z" fill="#e2001a"/>
    <path d="M369.7 224.8 A100 100 0 0 1 245 166.7 L287.8 149.8 A54 54 0 0 0 355.1 181.2 Z" fill="#ffffff"/>
    <circle cx="338" cy="130" r="46" fill="#1c1d22"/>
    <circle cx="338" cy="130" r="36" fill="#e2001a"/>
    <text x="338" y="133" text-anchor="middle" font-family="Raleway,sans-serif" font-size="8" font-weight="700" fill="#fff">PLORVEN</text>
    <g font-family="Raleway,sans-serif" font-weight="800" font-size="13">
      <text x="322" y="47" text-anchor="middle" fill="#fff">01</text>
      <text x="425" y="119" text-anchor="middle" fill="#222">02</text>
      <text x="352" y="223" text-anchor="middle" fill="#fff">03</text>
      <text x="250" y="148" text-anchor="middle" fill="#222">04</text>
    </g>
    <g font-family="Raleway,sans-serif" font-weight="700" font-size="5">
      <text x="0" y="0" text-anchor="middle" fill="#fff" transform="translate(282 86) rotate(-62)">VEHICLES</text>
      <text x="0" y="0" text-anchor="middle" fill="#222" transform="translate(375 64) rotate(45)">SMARTPHONES</text>
      <text x="0" y="0" text-anchor="middle" fill="#fff" transform="translate(396 172) rotate(150)">EMAIL</text>
      <text x="0" y="0" text-anchor="middle" fill="#222" transform="translate(300 189) rotate(222)">DOLLAR</text>
    </g>
    <!-- segment icons -->
    <g fill="none" stroke="#fff" stroke-width="1">
      <path d="M256 135 h16 v-4 l-3 -4 h-10 l-3 4 z"/><circle cx="259" cy="136" r="1.5"/><circle cx="269" cy="136" r="1.5"/>
      <path d="M374 200 h14 v10 h-14 z M374 200 l7 6 l7 -6"/>
    </g>
    <g fill="none" stroke="#222" stroke-width="1">
      <rect x="371" y="78" width="9" height="15" rx="1.5"/><line x1="374" y1="90" x2="377" y2="90"/>
      <circle cx="310" cy="203" r="6"/><text x="310" y="206" text-anchor="middle" font-family="Raleway,sans-serif" font-size="7" fill="#222" stroke="none">$</text>
    </g>
  </svg>
  <div class="cover-bar"></div>
  <h1 class="cover-title">LEAD <span>LIFE CYCLE</span><br>PROGRAM</h1>
  <p class="cover-sub">Credit Pre-Qualification &amp; Trade-In Appraisal</p>
</section>

<!-- Slide: Lead conversion goals -->
<section class="slide" style="left:529px;top:34px">
  <div class="title-bar"></div>
  <h2 class="slide-title">LEAD CONVERSION GOALS</h2>
  <div class="photo goals-photo" role="img" aria-label="Dealer handing car keys to a happy couple in a showroom"></div>
  <h3 class="goals-head">CONVERTING LEADS INTO SALES</h3>
  <div class="metric" style="top:77px"><div class="metric-label"><span>Natus error sit voluptatem accusantium dolo</span><span>90%</span></div><div class="metric-track"><div class="metric-fill" style="width:84%"></div></div></div>
  <div class="metric" style="top:102px"><div class="metric-label"><span>Nemo enim ipsam voluptatem quia voluptas</span><span>80%</span></div><div class="metric-track"><div class="metric-fill" style="width:73%"></div></div></div>
  <div class="metric" style="top:127px"><div class="metric-label"><span>Qostrum exercitationem ullam corporis suscipit</span><span>90%</span></div><div class="metric-track"><div class="metric-fill" style="width:68%"></div></div></div>
  <div class="metric" style="top:152px"><div class="metric-label"><span>Nor again is there anyone who loves or pursues or desires</span><span>85%</span></div><div class="metric-track"><div class="metric-fill" style="width:83%"></div></div></div>
  <div class="metric" style="top:176px"><div class="metric-label"><span>Natus error sit voluptatem accusantium dolo</span><span>80%</span></div><div class="metric-track"><div class="metric-fill" style="width:68%"></div></div></div>
  <div class="metric" style="top:201px"><div class="metric-label"><span>Quis nostrum exercitationem ullam corporis suscipi</span><span>50%</span></div><div class="metric-track"><div class="metric-fill" style="width:49%"></div></div></div>
  <footer class="footer"><div class="footer-left">(C) Copyright 2024 | All Rights Reserved</div><div class="footer-right">Pago 05 Of 08</div></footer>
</section>

<!-- Slide: Lead generation sources -->
<section class="slide" style="left:32px;top:325px">
  <div class="title-bar"></div>
  <h2 class="slide-title">LEAD GENERATION SOURCES</h2>
  <svg class="sources-art" viewBox="0 0 460 259" aria-hidden="true">
    <path d="M49.5 48 H268 L244 97 H49.5 A24.5 24.5 0 0 1 49.5 48 Z" fill="#e2001a"/>
    <path d="M262 52 H272 L290 72 L256 93 H246 Z" fill="#a50013"/>
    <path d="M270 52 H276 L294 72 L264 93 H256 Z" fill="#e2001a"/>
    <circle cx="49" cy="72" r="20" fill="#fff"/>
    <g fill="none" stroke="#333" stroke-width="0.9"><rect x="43" y="63" width="12" height="16" rx="1"/><line x1="46" y1="68" x2="52" y2="68"/><line x1="46" y1="71" x2="52" y2="71"/><path d="M46 75 l2 2 l4 -4"/></g>

    <path d="M81.5 111 H236 L214 160 H81.5 A24.5 24.5 0 0 1 81.5 111 Z" fill="#3a3a3a"/>
    <path d="M230 116 H238 L258 135 L226 155 H216 Z" fill="#262626"/>
    <circle cx="81" cy="135" r="20" fill="#fff"/>
    <g fill="none" stroke="#333" stroke-width="0.9"><rect x="72" y="129" width="18" height="12"/><path d="M72 129 l9 7 l9 -7"/></g>

    <path d="M112.5 176 H200 L178 225 H112.5 A24.5 24.5 0 0 1 112.5 176 Z" fill="#161616"/>
    <path d="M196 181 H206 L227 199 L193 221 H183 Z" fill="#000"/>
    <circle cx="112" cy="200" r="20" fill="#fff"/>
    <g fill="none" stroke="#333" stroke-width="0.9"><ellipse cx="112" cy="194" rx="7" ry="2.5"/><path d="M105 194 v10 a7 2.5 0 0 0 14 0 v-10"/><path d="M105 199 a7 2.5 0 0 0 14 0"/></g>

    <path d="M235 210 h4 v11 h4 l-6 7 l-6 -7 h4 z" fill="#111"/>
  </svg>
  <p class="source-name" style="left:79px;top:59px">PRE-QUALIFICATION TOOL<br>(FAST4LOAN)- HOW IT WORKS</p>
  <p class="source-copy" style="left:298px;top:62px">Converts Web Traffic into the highest<br>quality lead on the market</p>
  <p class="source-name" style="left:111px;top:117px">VORQEL EMAIL/MAIL<br>MARKETING – HOW IT<br>WORKS</p>
  <p class="source-copy" style="left:277px;top:109px">Delivers actionable leads from email marketing not<br>Just OPENS AND CLICKS. Show the text demo.<br>Audiences below</p>
  <ul class="source-list" style="left:277px;top:143px">
    <li>Past Sold Customers (Equity Targets)</li>
    <li>Past Service Onlu Department Customers (Conquest Sales)</li>
    <li>Unsold Leads (from previous interactions)</li>
  </ul>
  <p class="feed-line" style="left:233px;top:193px">Multiple Lead Sources Feeding into the Program</p>
  <footer class="footer"><div class="footer-left">(C) Copyright 2024 | All Rights Reserved</div><div class="footer-right">Pago 02 Of 08</div></footer>
</section>

<!-- Slide: Cross-offer -->
<section class="slide" style="left:529px;top:325px">
  <div class="title-bar"></div>
  <h2 class="slide-title">MAXIMIZE LEAD POTENTIAL WITH CROSS-OFFER<br>OPPORTUNITIES</h2>
  <div class="cross-photo" role="img" aria-label="Rising stacks of coins and rolled banknotes beside letter blocks spelling lead"></div>
  <footer class="footer"><div class="footer-left">(C) Copyright 2024 | All Rights Reserved</div><div class="footer-right">Pago 06 Of 08</div></footer>
</section>

<!-- Slide: Credit leads flow -->
<section class="slide" style="left:32px;top:616px">
  <div class="title-bar"></div>
  <h2 class="slide-title">CREDIT LEADS - PRE-QUALIFIED FLOW</h2>
  <div class="flow-photo" role="img" aria-label="Smiling customer checking a pre-qualification result on her phone at home"></div>
  <h3 class="flow-head">PRE-QUALIFIED LEADS:<br>OFFERING TRADE-IN APPRAISAL</h3>
  <svg class="flow-art" viewBox="0 0 460 259" aria-hidden="true">
    <path d="M175 97 C200 108 225 98 238 76" fill="none" stroke="#111" stroke-width="2.2" stroke-linecap="round"/>
    <path d="M230 76 L240 69 L242 81" fill="none" stroke="#111" stroke-width="2.2" stroke-linecap="round" stroke-linejoin="round"/>
    <path d="M242 86 H431 V112 L336.5 120 L242 112 Z" fill="#161616"/>
    <path d="M242 118 L336.5 126 L431 118 V160 L336.5 168 L242 160 Z" fill="#3a3a3a"/>
    <path d="M242 165 L336.5 173 L431 165 V212 L336.5 230 L242 212 Z" fill="#e2001a"/>
  </svg>
  <p class="flow-step" style="top:90px"><b>01</b>Customer pre-qualifies via Fast4Loan</p>
  <p class="flow-step" style="top:139px"><b>02</b>Receives credit approval</p>
  <p class="flow-step" style="top:192px"><b>03</b>Email and Mail</p>
  <footer class="footer"><div class="footer-left">(C) Copyright 2024 | All Rights Reserved</div><div class="footer-right">Pago 03 Of 08</div></footer>
</section>

<!-- Slide: Lifecycle representation -->
<section class="slide" style="left:32px;top:907px">
  <div class="title-bar"></div>
  <h2 class="slide-title">LIFECYCLE REPRESENTATION</h2>
  <p class="life-sub">CONTINUOUS ENGAGEMENT THROUGHOUT THE LEAD LIFE CYCLE</p>
  <svg class="life-art" viewBox="0 0 460 259" aria-hidden="true">
    <line x1="25" y1="144" x2="425" y2="144" stroke="#333" stroke-width="0.6"/>
    <g font-family="Raleway,sans-serif" font-weight="800" font-size="10" fill="#fff" text-anchor="middle">
      <circle cx="67" cy="144" r="24" fill="#f4a9b1"/><circle cx="67" cy="144" r="16" fill="#e2001a"/><text x="67" y="147.5">01</text>
      <circle cx="146" cy="144" r="24" fill="#c9c9c9"/><circle cx="146" cy="144" r="16" fill="#3a3a3a"/><text x="146" y="147.5">02</text>
      <circle cx="224" cy="144" r="24" fill="#f4a9b1"/><circle cx="224" cy="144" r="16" fill="#e2001a"/><text x="224" y="147.5">03</text>
      <circle cx="303" cy="144" r="24" fill="#c9c9c9"/><circle cx="303" cy="144" r="16" fill="#3a3a3a"/><text x="303" y="147.5">04</text>
      <circle cx="382" cy="144" r="24" fill="#f4a9b1"/><circle cx="382" cy="144" r="16" fill="#e2001a"/><text x="382" y="147.5">05</text>
    </g>
  </svg>
  <div class="life-note up" style="left:97px;top:69px">Sed ut perspiciatis unde omnis iste natus error sit voluptatem accusantium dolorem<strong>EXERCITATIONEM ULLAM</strong></div>
  <div class="life-note up" style="left:255px;top:69px">Sed ut perspiciatis unde omnis iste natus error sit voluptatem accusantium dolorem<strong>EXERCITATIONEM ULLAM</strong></div>
  <div class="life-note down" style="left:17px;top:178px"><strong>EXERCITATIONEM ULLAM</strong>Sed ut perspiciatis unde omnis iste natus error sit voluptatem accusantium dolorem</div>
  <div class="life-note down" style="left:171px;top:178px;width:110px"><strong>EXERCITATIONEM ULLAM</strong>Sed ut perspiciatis unde omnis iste natus error sit voluptatem accusantium dolorem</div>
  <div class="life-note down" style="left:329px;top:178px;width:110px"><strong>EXERCITATIONEM ULLAM</strong>Sed ut perspiciatis unde omnis iste natus error sit voluptatem accusantium dolorem que lauda ntium, totam rem</div>
  <footer class="footer"><div class="footer-left">(C) Copyright 2024 | All Rights Reserved</div><div class="footer-right">Pago 04 Of 08</div></footer>
</section>

</body>
</html>
```